professional business card design

Business card design. Photos have been uploaded and i am open to the designer choosing which photos to use. Would like the card to be mostyly in a grey scale design with black, whites, silver & grey colours. I have added copy of our flyer as would like on the back side of card our services to be listed. Do not use any bright colurs such as blue red green or yellow. i need to be able to edit the phone number and naem in the final card design submitted.

Target Market(s)

Clients

Industry/Entity Type

earhmovibng and transport

Contact Information for Business Card

Director Name, address, email, phone number and services

Colors

Designer to choose only greyscale colors for use in the design.

Requirements
Should not have
• no yellow, red, blue or green

```html
<!DOCTYPE html>
<html lang="en">
<head>
<meta charset="utf-8">
<title>Ridgeline Pty Ltd – Business Card</title>
<link href="https://fonts.googleapis.com/css2?family=Lato:wght@400;700&family=Open+Sans:wght@400;600&display=swap" rel="stylesheet">
<style>
  :root {
    --backdrop: #3b3937;
    --card-black: #0a0a0a;
    --panel-dark: #1a1a1a;
    --panel-mid: #3a3a3a;
    --silver: #d6d6d6;
    --silver-dim: #9a9a9a;
    --white: #ffffff;
  }
  * { margin: 0; padding: 0; box-sizing: border-box; }
  html, body { width: 1200px; height: 801px; overflow: hidden; background: var(--backdrop); }
  .canvas { position: relative; width: 1200px; height: 801px; }

  .card {
    position: absolute;
    width: 540px; height: 318px;
    border-radius: 18px;
    overflow: hidden;
    background: var(--card-black);
    box-shadow: 0 10px 28px rgba(0,0,0,.45);
  }
  .card--back { left: 40px; top: 242px; }
  .card--front { left: 620px; top: 242px; }

  /* back side */
  .back-texture {
    position: absolute; inset: 0;
    background: radial-gradient(ellipse at 50% 30%, var(--panel-mid) 0%, var(--panel-dark) 55%, var(--card-black) 100%);
  }
  .back-fleet-photo {
    position: absolute; left: 0; right: 0; top: 90px; height: 150px;
    background: linear-gradient(90deg, #2a2a2a 0%, #444 30%, #2e2e2e 60%, #1c1c1c 100%);
    opacity: .85;
  }
  .brand {
    position: absolute; left: 0; right: 0;
    text-align: center;
    font-family: 'Lato', sans-serif; font-weight: 700;
    color: var(--silver);
    letter-spacing: 1px;
  }
  .card--back .brand { top: 30px; font-size: 44px; }
  .brand-suffix {
    position: absolute; font-family: 'Lato', sans-serif; font-weight: 700;
    color: var(--silver); font-size: 13px;
  }
  .card--back .brand-suffix { left: 346px; top: 86px; }

  .services {
    position: absolute; left: 0; right: 0; top: 150px;
    text-align: center;
    font-family: 'Lato', sans-serif; font-size: 14.5px; line-height: 27px;
    color: var(--white);
  }
  .tick { display: inline-block; width: 13px; height: 13px; vertical-align: -2px; margin: 0 4px; }

  /* front side */
  .front-texture {
    position: absolute; inset: 0;
    background: radial-gradient(ellipse at 45% 25%, var(--panel-mid) 0%, var(--panel-dark) 60%, var(--card-black) 100%);
  }
  .front-shape { position: absolute; inset: 0; }
  .card--front .brand { top: 48px; font-size: 50px; }
  .card--front .brand-suffix { left: 336px; top: 110px; font-size: 14px; }

  .person { position: absolute; left: 70px; top: 222px; font-family: 'Open Sans', sans-serif; }
  .person-name { font-size: 25px; font-weight: 600; color: var(--silver-dim); letter-spacing: .5px; }
  .person-role { font-size: 15px; color: var(--silver); text-align: right; margin-top: -2px; }

  .divider { position: absolute; left: 298px; top: 196px; width: 1px; height: 86px; background: var(--silver-dim); }

  .contact {
    position: absolute; left: 314px; top: 186px;
    font-family: 'Open Sans', sans-serif; color: var(--silver); font-size: 13px;
    list-style: none;
  }
  .contact li { display: flex; align-items: flex-start; gap: 9px; margin-bottom: 6px; line-height: 18px; }
  .contact .phone { font-size: 16px; font-weight: 600; color: var(--white); }
  .contact svg { width: 12px; height: 12px; margin-top: 3px; flex: none; }
</style>
</head>
<body>
<main class="canvas">

  <section class="card card--back" aria-label="Business card back: services">
    <div class="back-texture" role="img" aria-label="Dark perforated metal texture"></div>
    <div class="back-fleet-photo" role="img" aria-label="Greyscale photo of a road train truck with trailers"></div>
    <div class="brand">Ridgeline</div>
    <div class="brand-suffix">Pty Ltd</div>
    <p class="services">
      Over Size Loads / Hot Shot Loads<br>
      Heavy Vehicle Recovery Services<svg class="tick" viewBox="0 0 14 14"><circle cx="7" cy="7" r="7" fill="#fff"/><path d="M3.8 7.2l2.2 2.2 4.2-4.4" stroke="#000" stroke-width="1.8" fill="none"/></svg>Poatable Water Deliveries<br>
      Road Building / Maintenance<svg class="tick" viewBox="0 0 14 14"><circle cx="7" cy="7" r="7" fill="#fff"/><path d="M3.8 7.2l2.2 2.2 4.2-4.4" stroke="#000" stroke-width="1.8" fill="none"/></svg>Earthworks<svg class="tick" viewBox="0 0 14 14"><circle cx="7" cy="7" r="7" fill="#fff"/><path d="M3.8 7.2l2.2 2.2 4.2-4.4" stroke="#000" stroke-width="1.8" fill="none"/></svg>Sand &amp; Metal Supply &amp; Cartage<br>
      Road Train Tippers<svg class="tick" viewBox="0 0 14 14"><circle cx="7" cy="7" r="7" fill="#fff"/><path d="M3.8 7.2l2.2 2.2 4.2-4.4" stroke="#000" stroke-width="1.8" fill="none"/></svg>Road Train Tankers<svg class="tick" viewBox="0 0 14 14"><circle cx="7" cy="7" r="7" fill="#fff"/><path d="M3.8 7.2l2.2 2.2 4.2-4.4" stroke="#000" stroke-width="1.8" fill="none"/></svg>Road Train Flat Tops<br>
      Drop Dect Trailers<svg class="tick" viewBox="0 0 14 14"><circle cx="7" cy="7" r="7" fill="#fff"/><path d="M3.8 7.2l2.2 2.2 4.2-4.4" stroke="#000" stroke-width="1.8" fill="none"/></svg>Mine Site Accredited Equipment and Operators
    </p>
  </section>

  <section class="card card--front" aria-label="Business card front: contact">
    <div class="front-texture" role="img" aria-label="Dark perforated metal texture"></div>
    <svg class="front-shape" viewBox="0 0 540 318" preserveAspectRatio="none">
      <defs>
        <linearGradient id="silverLine" x1="0" x2="1">
          <stop offset="0" stop-color="#f2f2f2"/>
          <stop offset=".5" stop-color="#9c9c9c"/>
          <stop offset="1" stop-color="#e0e0e0"/>
        </linearGradient>
      </defs>
      <polygon points="0,205 540,100 540,318 0,318" fill="#0a0a0a"/>
      <polygon points="0,198 540,93 540,99 0,206" fill="url(#silverLine)"/>
    </svg>
    <div class="brand">Ridgeline</div>
    <div class="brand-suffix">Pty Ltd</div>

    <div class="person">
      <div class="person-name">DANIEL BROOKS</div>
      <div class="person-role">Director &amp; Founder</div>
    </div>
    <div class="divider"></div>
    <ul class="contact">
      <li><svg viewBox="0 0 12 12"><path d="M6 1a3.5 3.5 0 0 0-3.5 3.5C2.5 7.5 6 11 6 11s3.5-3.5 3.5-6.5A3.5 3.5 0 0 0 6 1zm0 5a1.5 1.5 0 1 1 0-3 1.5 1.5 0 0 1 0 3z" fill="#bbb"/></svg><span>Your Address, City<br>State, Zip 1235</span></li>
      <li><svg viewBox="0 0 12 12"><path d="M3 1l2 2.5-1 1.2a7 7 0 0 0 3.3 3.3l1.2-1L11 9l-1.4 1.8C5.5 10.5 1.5 6.5 1.2 2.4z" fill="#bbb"/></svg><span class="phone">(123) 456-7890</span></li>
      <li><svg viewBox="0 0 12 12"><rect x="1" y="2.5" width="10" height="7" fill="#bbb"/><path d="M1 2.5l5 4 5-4" stroke="#222" fill="none"/></svg><span>info@yourwebsite.com</span></li>
    </ul>
  </section>

</main>
</body>
</html>
```